Marine Services Letterhead design

We need a letterhead design for an Australian owned company in Victoria named K+T Harbour Works Pty Ltd. We provide linesmen and launches to assist the large ships that come into port.
Our colour is orange.
The final design should have a strong nautical theme and communicate safety and reliability.
I would like to use the letter head on invoices so it should print to pdf well.

Target Market(s)

Owners and representatives of shipping companies. It is not for general public

Industry/Entity Type

Nautical

Requirements
Must have
• A shipping theme, not overly complicated, featuring safety orange colours but not all orange of course.
The letterhead should just sit at the top of the page so I can use for invoices.
Nice to have
• Something elegant and stylish
Should not have
• cartoons or pop art

```html
<!DOCTYPE html>
<html lang="en">
<head>
<meta charset="utf-8">
<title>K+T Harbour Works Pty Ltd – Letterhead</title>
<link rel="stylesheet" href="https://fonts.googleapis.com/css2?family=Cinzel:wght@500&family=Open+Sans:wght@400&display=swap">
<style>
  :root {
    --sea-green: #93c5a2;
    --paper: #ffffff;
    --ink: #2b2b2b;
    --footer-bg: #1e1d1b;
    --footer-text: #ffffff;
    --frame: #ffffff;
    --mark-fill: #e89a3c;
  }
  * { box-sizing: border-box; margin: 0; padding: 0; }
  html, body {
    width: 883px;
    height: 1200px;
    overflow: hidden;
    background: var(--paper);
  }
  .letterhead {
    position: relative;
    width: 883px;
    height: 1200px;
    background: var(--paper);
  }
  .header-band {
    position: absolute;
    top: 0; left: 0;
    width: 100%;
    height: 101px;
    background: var(--sea-green);
  }
  .brand-block {
    position: absolute;
    top: 20px;
    left: 350px;
    width: 184px;
    height: 171px;
    background: var(--frame);
    padding: 10px;
  }
  .brand-tile {
    width: 100%;
    height: 100%;
    background: var(--sea-green);
    display: flex;
    flex-direction: column;
    align-items: center;
    justify-content: center;
    gap: 12px;
  }
  .brand-square {
    width: 34px;
    height: 34px;
    background: var(--mark-fill);
  }
  .brand-name {
    font-family: "Cinzel", serif;
    font-weight: 500;
    font-size: 15px;
    line-height: 1.3;
    color: var(--ink);
    text-align: center;
  }
  .company-name {
    position: absolute;
    top: 58px;
    right: 12px;
    font-family: "Cinzel", serif;
    font-weight: 500;
    font-size: 18px;
    letter-spacing: 0.5px;
    color: var(--ink);
    white-space: nowrap;
  }
  .footer-band {
    position: absolute;
    left: 0; bottom: 0;
    width: 100%;
    height: 45px;
    background: var(--footer-bg);
    display: flex;
    align-items: center;
    justify-content: center;
    gap: 12px;
    font-family: "Open Sans", sans-serif;
    font-size: 15px;
    color: var(--footer-text);
  }
  .contact-item {
    display: flex;
    align-items: center;
    gap: 4px;
  }
  .contact-item svg { width: 12px; height: 14px; fill: var(--footer-text); }
  .divider {
    width: 1px;
    height: 26px;
    background: var(--footer-text);
  }
</style>
</head>
<body>
  <main class="letterhead">
    <header class="header-band">
      <p class="company-name">K+T Harbour Works Pty Ltd</p>
    </header>
    <div class="brand-block">
      <div class="brand-tile">
        <span class="brand-square"></span>
        <span class="brand-name">K+T Harbour<br>Works</span>
      </div>
    </div>
    <footer class="footer-band">
      <span class="contact-item">
        <svg viewBox="0 0 12 14" aria-hidden="true"><path d="M3 0.5 L5 3.5 L3.8 5 C4.5 7 5.5 8.6 7.2 9.8 L8.6 8.6 L11.5 10.8 L10 13.3 C5 12.5 1 7.5 0.8 2 Z"/></svg>
        1300 418 207
      </span>
      <span class="contact-item">
        <svg viewBox="0 0 12 14" aria-hidden="true"><path d="M6 0 C2.7 0 0.5 2.3 0.5 5.2 C0.5 8.8 6 14 6 14 C6 14 11.5 8.8 11.5 5.2 C11.5 2.3 9.3 0 6 0 Z M6 7.2 A2 2 0 1 1 6 3.2 A2 2 0 1 1 6 7.2 Z"/></svg>
        PO Box 214 Merricks 3916
      </span>
      <span class="divider"></span>
      <span class="contact-item">ABN: 48203915667</span>
    </footer>
  </main>
</body>
</html>
```